New Bicycle shop business card

Hi!
I'm looking for a business card for my new proffesional bike mechanics shop. This shop is only for fixing broken bikes and not selling bikes.
Peferbly a modern and sleek and modern design.
Colors: black, grey, red, white
Information:
Name: Rijwielwerkplaats Vanhoutte
Shop owner: Bart Vanhoutte & Marieke Segers
Website: www.rijwielwerkplaats-vanhoutte.be
Email: info@rijwielwerkplaats-vanhoutte.be
Phone number: +32471902368
Street adres: Kerkweg 46
9940 Bellebeke
Slogan/shop information: Herstellingen van alle merken.
Logo: see files.
Target Market(s)
People who seek a mechanic to fix or upgrade their bikes.
Contact Information for Business Card
Information:
Website: info@rijwielwerkplaats-vanhoutte.be
9940 Bellebeke
Logo: see files.

```html
<!DOCTYPE html>
<html lang="nl">
<head>
<meta charset="utf-8">
<title>Rijwielwerkplaats Vanhoutte – visitekaartje</title>
<link rel="stylesheet" href="https://fonts.googleapis.com/css2?family=Fira+Sans:wght@400;600&display=swap">
<style>
  :root {
    --red: #d92a38;
    --black: #1b1415;
    --grey: #a9a9a9;
    --white: #ffffff;
    --paper: #e8ecec;
  }
  * { margin: 0; padding: 0; box-sizing: border-box; }
  html, body { width: 1200px; height: 900px; overflow: hidden; }
  body {
    background: var(--paper);
    font-family: "Fira Sans", Arial, sans-serif;
    position: relative;
  }
  .card {
    position: absolute;
    background: var(--red);
    box-shadow: 0 2px 0 #cfcfcf, 0 4px 0 #c4c4c4, 0 12px 26px rgba(0,0,0,0.14);
    overflow: hidden;
  }
  .card-front {
    left: 80px; top: 300px; width: 540px; height: 310px;
    display: flex; align-items: center; justify-content: center;
  }
  .front-brand {
    display: flex; align-items: center; gap: 14px;
    color: var(--black);
    font-weight: 600; font-size: 27px; letter-spacing: 0.5px;
  }
  .brand-mark {
    width: 18px; height: 18px; border-radius: 50%;
    background: var(--black); flex: none;
  }
  .card-back {
    left: 740px; top: 180px; width: 310px; height: 540px;
    color: var(--white);
  }
  .back-band {
    height: 150px; background: var(--black);
    display: flex; align-items: center; justify-content: flex-end;
    padding: 0 26px; gap: 10px;
  }
  .back-band .brand-name {
    font-weight: 600; font-size: 16px; text-align: right; line-height: 1.25;
  }
  .back-band .brand-mark { background: var(--red); width: 22px; height: 22px; }
  .back-body { padding: 30px 28px 0; }
  .shop-name { font-weight: 600; font-size: 19px; line-height: 1.2; }
  .owners { font-size: 12.5px; margin-top: 4px; }
  .address { font-size: 13px; line-height: 1.45; margin-top: 22px; }
  .contact-icons { display: flex; gap: 12px; margin-top: 14px; }
  .contact-icons svg { width: 12px; height: 12px; fill: var(--white); }
  .contact-lines { font-size: 12.5px; line-height: 1.55; margin-top: 8px; }
  .divider {
    width: 150px; height: 1px; background: var(--white);
    margin-top: 34px;
  }
  .slogan { font-size: 13px; margin-top: 26px; }
</style>
</head>
<body>
  <section class="card card-front" aria-label="Voorkant visitekaartje">
    <div class="front-brand">
      <span class="brand-mark"></span>
      <span>Rijwielwerkplaats Vanhoutte</span>
    </div>
  </section>

  <section class="card card-back" aria-label="Achterkant visitekaartje">
    <div class="back-band">
      <span class="brand-name">Rijwielwerkplaats<br>Vanhoutte</span>
      <span class="brand-mark"></span>
    </div>
    <div class="back-body">
      <h1 class="shop-name">Rijwielwerkplaats Vanhoutte</h1>
      <p class="owners">Owner: Bart Vanhoutte &amp; Marieke Segers</p>
      <p class="address">Kerkweg 46<br>9940 Bellebeke</p>
      <div class="contact-icons" aria-hidden="true">
        <svg viewBox="0 0 12 12"><path d="M2.5 0.8l2 2.2-1 1.3c.7 1.6 2 2.9 3.6 3.6l1.3-1 2.2 2-1.4 2.1C5 10.6 1.4 7 .4 2.2z"/></svg>
        <svg viewBox="0 0 12 12"><path d="M0 2.5h12v7H0z M0.6 2.9L6 6.6l5.4-3.7" stroke="#d92a38" stroke-width="0.9"/></svg>
        <svg viewBox="0 0 12 12"><circle cx="6" cy="6" r="5.5"/><path d="M0.5 6h11M6 .5c-2.5 3-2.5 8 0 11M6 .5c2.5 3 2.5 8 0 11" stroke="#d92a38" stroke-width="0.8" fill="none"/></svg>
      </div>
      <p class="contact-lines">
        +32471902368<br>
        info@rijwielwerkplaats-vanhoutte.be<br>
        www.rijwielwerkplaats-vanhoutte.be
      </p>
      <div class="divider"></div>
      <p class="slogan">Herstellingen van alle merken.</p>
    </div>
  </section>
</body>
</html>
```